Pine Ledge Traders, LLC- Global Beverage Company with 100% Cold Chain Logistics

Hey All, My Name is Dale, I am a young business owner in a competitive export space, but my niche is that I am shipping all of my beer around the world, "100% Cold Chain". This model is more costly, but it protects the integrity of the beer itself and will give folks in foreign countries the best representation of what US Craft Beer has to offer.

I am not a branding guy and don't claim to be one, I am a salesperson first, and will be referring to all of you to create something great that will be memorable.

I am looking for a basic Business Card Design for my Craft Beer Export company. I sell US Craft Beer in several countries around the globe. Austrailia, China, Taiwan, Chile, France, New Zealand... to name a few.

I am looking for a sleek, modern, and fresh design. Quickly!

Thanks for your consideration!

Cheers,

Dale

Target Market(s)

International

Contact Information for Business Card

Dale Corrigan
Founder- Roaming Hops Guy
Dale@PineLedgeTraders.example
@RoamingHopsGuy- Instagram only
www.Pineledgetraders.example
@PineLedgeTradersAU- Instagram Only

Font styles to use
Serif

Colors
0592cd
ffffff

Requirements
Must have
• Name-
• Title-
• Email-
• Social Media Handle-
• Company Website-
Nice to have
• Nice Logo/ Images on Card
Should not have
• Tacky Beer Images

```html
<!DOCTYPE html>
<html lang="en">
<head>
<meta charset="utf-8">
<title>Pine Ledge Traders – Business Card</title>
<link rel="stylesheet" href="https://fonts.googleapis.com/css2?family=Outfit:wght@500&family=Roboto:wght@400&display=swap">
<style>
  :root {
    --bg: #b9b9b9;
    --card-white: #f4f4f4;
    --brand-blue: #0592cd;
    --back-blue: #2189b4;
    --text-dark: #333333;
    --text-grey: #666a6d;
    --rule-grey: #8a8a8a;
    --white: #ffffff;
  }
  * { margin: 0; padding: 0; box-sizing: border-box; }
  html, body { width: 1200px; height: 1200px; overflow: hidden; }
  body {
    background: var(--bg);
    position: relative;
    font-family: "Roboto", Arial, sans-serif;
  }
  .card {
    position: absolute;
    top: 310px;
    width: 364px;
    height: 594px;
    border-radius: 18px;
    overflow: hidden;
  }
  .card-front { left: 234px; background: var(--card-white); }
  .card-back { left: 627px; width: 370px; background: var(--back-blue); }

  .brand-mark {
    position: absolute;
    left: 50%; top: 66px;
    transform: translateX(-50%);
    width: 58px; height: 58px;
    background: var(--brand-blue);
  }
  .brand-name {
    position: absolute;
    top: 150px; left: 0; width: 100%;
    text-align: center;
    color: var(--brand-blue);
    font-size: 31px;
    line-height: 36px;
    letter-spacing: 1px;
    text-transform: uppercase;
  }
  .tagline {
    position: absolute;
    top: 225px; left: 0; width: 100%;
    text-align: center;
    color: var(--text-grey);
    font-size: 15.5px;
    letter-spacing: 2.2px;
  }
  .person-name {
    position: absolute;
    top: 340px; left: 0; width: 100%;
    text-align: center;
    font-family: "Outfit", Arial, sans-serif;
    font-weight: 500;
    font-size: 26px;
    color: var(--brand-blue);
  }
  .person-title {
    position: absolute;
    top: 372px; left: 0; width: 100%;
    text-align: center;
    font-size: 16.5px;
    color: var(--text-dark);
  }
  .divider {
    position: absolute;
    left: 0; width: 100%;
    display: flex; justify-content: center; align-items: center; gap: 6px;
  }
  .divider .rule { height: 1px; width: 52px; background: var(--rule-grey); }
  .divider-contact { top: 415px; }
  .divider-social { top: 503px; }
  .social-square { width: 20px; height: 20px; background: #3b5a9a; margin: 0 4px; }
  .contact-lines {
    position: absolute;
    top: 439px; left: 0; width: 100%;
    text-align: center;
    font-size: 16.5px;
    line-height: 22px;
    color: var(--text-dark);
  }
  .social-handle {
    position: absolute;
    top: 527px; left: 0; width: 100%;
    text-align: center;
    font-size: 16.5px;
    color: var(--text-dark);
  }

  .back-pattern { position: absolute; inset: 0; background: var(--back-blue); }
  .back-brand {
    position: absolute;
    left: 196px; top: 388px;
    width: 115px;
    color: var(--white);
    font-size: 19px;
    line-height: 23px;
    text-transform: uppercase;
    text-align: center;
  }
</style>
</head>
<body>
  <section class="card card-front">
    <div class="brand-mark"></div>
    <div class="brand-name">Pine Ledge<br>Traders</div>
    <div class="tagline">GLOBAL BEVERAGE COMPANY</div>

    <div class="person-name">Dale Corrigan</div>
    <div class="person-title">Founder - Roaming Hops Guy</div>

    <div class="divider divider-contact">
      <span class="rule"></span>
      <svg width="38" height="14" viewBox="0 0 38 14" aria-hidden="true">
        <rect x="1" y="1.5" width="14" height="11" fill="var(--brand-blue)"/>
        <polyline points="1.5,2 8,8 14.5,2" fill="none" stroke="#fff" stroke-width="1.3"/>
        <circle cx="30" cy="7" r="6.5" fill="var(--brand-blue)"/>
        <ellipse cx="30" cy="7" rx="2.8" ry="6.3" fill="none" stroke="#fff" stroke-width="1"/>
        <line x1="23.5" y1="7" x2="36.5" y2="7" stroke="#fff" stroke-width="1"/>
      </svg>
      <span class="rule"></span>
    </div>
    <div class="contact-lines">
      Dale@PineLedgeTraders.example<br>
      www.Pineledgetraders.example
    </div>

    <div class="divider divider-social">
      <span class="rule"></span>
      <span class="social-square"></span>
      <span class="rule"></span>
    </div>
    <div class="social-handle">@RoamingHopsGuy</div>
  </section>

  <section class="card card-back">
    <div class="back-pattern" role="img" aria-label="Repeating brand monogram pattern in tones of blue"></div>
    <div class="back-brand">Pine Ledge<br>Traders</div>
  </section>
</body>
</html>
```